Business card for medical clinic

I need an upmarket, modern medical/health business card for my clinic

Contact Information for Business Card

name, address, email, qr code

```html
<!DOCTYPE html>
<html lang="en">
<head>
<meta charset="utf-8">
<title>Meridian Care Partners – Business Card</title>
<link href="https://fonts.googleapis.com/css2?family=Montserrat:wght@400;500;700&display=swap" rel="stylesheet">
<style>
  :root {
    --backdrop: #6b6b6b;
    --card-white: #ffffff;
    --navy: #1f3552;
    --navy-deep: #233650;
    --blue-mid: #2f7aa8;
    --blue-bright: #29abe2;
    --text-grey: #4a4a4a;
    --rule-blue: #29a3dc;
  }
  * { margin: 0; padding: 0; box-sizing: border-box; }
  html, body {
    width: 1200px; height: 800px; overflow: hidden;
    background: var(--backdrop);
    font-family: "Montserrat", sans-serif;
  }
  .canvas {
    width: 1200px; height: 800px;
    display: flex; align-items: center; justify-content: center; gap: 48px;
  }
  .card {
    position: relative;
    width: 525px; height: 300px;
    border-radius: 18px;
    overflow: hidden;
    box-shadow: 0 14px 30px rgba(0,0,0,0.35);
  }

  /* Front */
  .card-front {
    background: var(--card-white);
    border-bottom: 6px solid var(--rule-blue);
  }
  .brand-lockup {
    position: absolute; left: 36px; top: 68px;
    display: flex; align-items: center; gap: 12px;
    width: 230px;
  }
  .brand-dot {
    width: 16px; height: 16px; border-radius: 50%;
    background: var(--navy); flex: none;
  }
  .brand-name {
    font-weight: 700; font-size: 16px; line-height: 21px; letter-spacing: 1.5px;
    color: var(--navy); text-transform: uppercase;
  }
  .person {
    position: absolute; right: 36px; top: 40px; text-align: right;
  }
  .person-name {
    font-weight: 700; font-size: 19px; color: var(--navy);
    letter-spacing: 0.5px; text-transform: uppercase;
  }
  .person-title {
    font-weight: 400; font-size: 13px; color: var(--text-grey); margin-top: 2px;
  }
  .divider {
    position: absolute; left: 36px; right: 36px; top: 172px;
    height: 1px; background: var(--rule-blue);
  }
  .contact-list {
    position: absolute; left: 36px; top: 190px;
    list-style: none;
  }
  .contact-list li {
    display: flex; align-items: center; gap: 9px;
    font-size: 13px; color: var(--text-grey); line-height: 22px;
  }
  .contact-list svg { width: 12px; height: 12px; flex: none; }
  .address {
    position: absolute; right: 36px; top: 190px; text-align: right;
    font-size: 13px; color: var(--text-grey); line-height: 22px;
    font-style: normal;
  }

  /* Back */
  .card-back {
    background: linear-gradient(105deg, var(--navy-deep) 0%, var(--blue-mid) 55%, var(--blue-bright) 100%);
    display: flex; align-items: center; justify-content: center;
  }
  .back-lockup { display: flex; align-items: center; gap: 16px; }
  .back-lockup .brand-dot {
    width: 24px; height: 24px; background: none; border: 3px solid #ffffff;
  }
  .back-lockup .brand-name {
    color: #ffffff; font-size: 24px; line-height: 30px; letter-spacing: 2.5px;
  }
</style>
</head>
<body>
<main class="canvas">
  <section class="card card-front">
    <div class="brand-lockup">
      <span class="brand-dot"></span>
      <span class="brand-name">Meridian Care<br>Partners</span>
    </div>
    <div class="person">
      <div class="person-name">Adrian Cole</div>
      <div class="person-title">President</div>
    </div>
    <div class="divider"></div>
    <ul class="contact-list">
      <li>
        <svg viewBox="0 0 24 24" fill="var(--rule-blue)"><path d="M6.6 10.8a15 15 0 0 0 6.6 6.6l2.2-2.2a1 1 0 0 1 1-.25 11.4 11.4 0 0 0 3.6.57 1 1 0 0 1 1 1V20a1 1 0 0 1-1 1A17 17 0 0 1 3 4a1 1 0 0 1 1-1h3.5a1 1 0 0 1 1 1 11.4 11.4 0 0 0 .57 3.6 1 1 0 0 1-.25 1z"/></svg>
        555-310-4872
      </li>
      <li>
        <svg viewBox="0 0 24 24" fill="var(--rule-blue)"><path d="M2 5h20v14H2z M2 5l10 8 10-8" stroke="#fff" stroke-width="1.5"/></svg>
        adrian@meridiancare.com
      </li>
      <li>
        <svg viewBox="0 0 24 24"><circle cx="12" cy="12" r="10" fill="var(--rule-blue)"/><path d="M2 12h20M12 2c3 3 3 17 0 20M12 2c-3 3-3 17 0 20" stroke="#fff" stroke-width="1.3" fill="none"/></svg>
        www.meridiancare.com
      </li>
    </ul>
    <address class="address">
      1820 Harbor Crest Drive<br>
      Bayview CA 90210
    </address>
  </section>

  <section class="card card-back">
    <div class="back-lockup">
      <span class="brand-dot"></span>
      <span class="brand-name">Meridian Care Partners</span>
    </div>
  </section>
</main>
</body>
</html>
```